Chai Tea Company needs a Tea Packaging Box Design

Tea Packaging
Dimensions of the Tea Packaging Box: Height 13 cm; Width 8.5 cm; Depth 7 cm
Individual Teabag Packet/ Sachet: Width 6.5 cm; Length 8.25 cm
We are looking for a new tea packaging design, for our tea business. The material of the box is cardboard. We are also looking for a design that will be on each individual tea bag sachet/packet that goes into the box. This design will be very similar to what you design for the tea packaging box.
Product Info:
Our tea company is called “Velmora Brew”. We sell two types of Chai Tea, once called “Velmora Gold” and one called “Velmora Meadow”. The Velmora Gold has caffeine, while the Velmora Meadow is Naturally Caffeine Free. The Velmora Gold has a black tea base, while the Velmora Meadow has a Rooibos tea base. We will need two tea packaging designs, one for each Chai Tea flavour. The designs for both the teas can be similar, but make sure that you can easily distinguish one from the other (example: make them have different colours or pictures). Both the chai teas, come from the same product line.
Tea Packaging Design:
We are looking for high end tea packaging. We produce high quality teas, and we would like to portray this in our tea packaging. Our teas are made with no artificial flavourings, natural flavourings, or preservatives, so we would also like a natural, organic, high quality look to our tea packaging. Our current logo is a llama. It would be great if you could make the current logo more polished and well made. If you feel that the llama is not well suited or you would like to design the llama differently, we are open to your creative ideas.
General Basic Info:
Keep in mind, we will have both English and French writing on the tea packaging. You do not need to worry about the French writing (we will do the translation), just make sure there is room for it. However, if you feel that you are capable and knowledgeable of incorporating both French and English language into the tea packaging that would be of great help and value.
Back of the Box:
- Will have ingredients and brewing instructions. Basic brewing instructions are: “Add hot water to teabag. Steep for 5-7 minutes, depending on strength preferred. Add milk and your choice of sweetener. Enjoy! See inside panel of box for more detailed instructions”. (The basic brewing instructions, can further be polished or written in a more creative or professional manner).
Front of the Box:
- Will have company name, type of tea, little description of the tea
- 18 teabags
- 54 g (1.9 OZ)
- Should state that this is a product of Alberta, Canada.
Side of the Box:
Any creative wording, slogan, or description about the tea, or whatever you feel would be good on the side of the box.
On the inside flap of the side of the box, there will be detailed instructions on how to brew the tea. These will be different from the simplified brewing instructions on the back of the box. I have attached the advanced brewing instructions as a file. These instructions can further be simplified or reduced to make it easier and cleaner for the consumers to read.
Individual Tea Sachets/ Packets
- These will have a matching look and design of the tea box packaging, except on a smaller scale. Each individual sachet will have the company name, type of tea, little description of the tea in the front of the sachet, while the back will contain the ingredients, and basic brewing instructions.
I have attached a few files, with the dimensions, ingredients, detailed brewing directions, and current logo of the business.
If you have any questions, about the design or packaging please let me know. The winning designer will be required to do a few additional tweaks to finalize the product. Thank you for your time and happy designing!

```html
<!DOCTYPE html>
<html lang="en">
<head>
<meta charset="utf-8">
<title>Velmora Brew – Velmora Gold Packaging</title>
<link rel="stylesheet" href="https://fonts.googleapis.com/css2?family=Josefin+Sans:wght@400;600&family=Cormorant+Garamond:ital,wght@1,600&display=swap">
<style>
  :root {
    --bg: #e6e6e4;
    --paper: #f6f5f1;
    --kraft-dark: #7c5f33;
    --kraft: #9a7b48;
    --kraft-light: #b09260;
    --ink-blue: #557d8e;
    --ink-soft: #8fb3c2;
    --ink-dark: #3f4a4f;
    --gold: #b8963e;
    --sans: "Josefin Sans", sans-serif;
    --serif: "Cormorant Garamond", serif;
  }
  * { box-sizing: border-box; margin: 0; padding: 0; }
  html, body { width: 1200px; height: 1000px; overflow: hidden; background: var(--bg); }
  .canvas { position: relative; width: 1200px; height: 1000px; }

  .panel {
    position: absolute;
    display: grid;
    grid-template-columns: 52px 1fr 52px;
    grid-template-rows: 100%;
    background: var(--paper);
    box-shadow: 0 10px 30px rgba(0,0,0,.12);
    overflow: hidden;
  }
  .kraft-band {
    background: linear-gradient(160deg, var(--kraft-light), var(--kraft) 45%, var(--kraft-dark));
  }
  .panel-body {
    display: flex; flex-direction: column; align-items: center;
    text-align: center; color: var(--ink-blue); font-family: var(--sans);
    min-width: 0; overflow: hidden;
  }

  .flap {
    position: absolute; height: 56px;
    display: grid; grid-template-columns: 52px 1fr 52px;
    background: var(--paper);
    box-shadow: 0 4px 14px rgba(0,0,0,.08);
  }
  .flap .panel-body { justify-content: center; }

  .brand-mark { display: flex; align-items: center; justify-content: center; gap: 10px; white-space: nowrap; }
  .brand-dot { flex: none; width: 12px; height: 12px; border-radius: 50%; background: var(--ink-blue); }
  .brand-name { font-family: var(--sans); font-weight: 600; color: var(--ink-blue); letter-spacing: .04em; }

  /* back panel */
  .back { left: 60px; top: 240px; width: 340px; height: 580px; }
  .back .panel-body { padding: 34px 16px 16px; align-items: flex-start; text-align: left; color: var(--ink-dark); }
  .back .brand-mark { align-self: center; margin-bottom: 12px; }
  .back .brand-name { font-size: 20px; }
  .back-title { align-self: center; font-weight: 600; font-size: 12px; letter-spacing: .1em; margin-bottom: 12px; }
  .back-intro { font-size: 10.5px; line-height: 1.45; text-transform: uppercase; margin-bottom: 10px; }
  .back h3 { font-size: 10.5px; font-weight: 600; letter-spacing: .06em; margin: 6px 0 4px; }
  .back ul, .back ol { font-size: 9px; line-height: 1.45; text-transform: uppercase; padding-left: 14px; }
  .back ul { list-style: none; padding-left: 0; }

  /* front panel */
  .front { left: 430px; top: 240px; width: 340px; height: 580px; }
  .front-flap { left: 430px; top: 172px; width: 340px; }
  .front-flap .brand-name { font-size: 15px; }
  .front .panel-body { padding: 26px 12px 20px; }
  .lang-row { display: flex; gap: 10px; align-items: center; font-size: 12px; letter-spacing: .08em; font-weight: 600; }
  .lang-sep { width: 7px; height: 7px; background: var(--ink-blue); }
  .caffeine-row { display: flex; justify-content: space-between; width: 190px; font-size: 8.5px; letter-spacing: .08em; margin-top: 3px; }
  .product-name { font-family: var(--serif); font-style: italic; font-weight: 600; font-size: 40px; color: var(--ink-blue); line-height: 1; margin: 14px 0 6px; white-space: nowrap; }
  .description { font-size: 10px; line-height: 1.35; letter-spacing: .05em; text-transform: uppercase; font-weight: 600; color: var(--ink-blue); }
  .gold-rule { width: 200px; height: 1px; background: var(--gold); margin: 8px 0 6px; }
  .description-fr { font-size: 8px; line-height: 1.4; letter-spacing: .04em; color: var(--gold); text-transform: uppercase; }
  .front .brand-mark { margin: 96px 0 60px; }
  .front .brand-dot { width: 16px; height: 16px; }
  .front .brand-name { font-size: 26px; }
  .count { font-family: var(--serif); font-size: 34px; color: var(--ink-dark); line-height: 1; }
  .count-label { font-size: 13px; letter-spacing: .1em; color: var(--ink-dark); }
  .small-print { font-size: 8px; letter-spacing: .06em; color: var(--ink-dark); text-transform: uppercase; line-height: 1.6; white-space: nowrap; }
  .net-weight { font-size: 10px; letter-spacing: .08em; color: var(--ink-dark); margin-top: 6px; }

  /* sachet */
  .sachet {
    left: 810px; top: 420px; width: 320px; height: 260px;
    grid-template-columns: 1fr; grid-template-rows: 36px 1fr 36px;
  }
  .sachet .panel-body { padding: 10px 16px; justify-content: center; gap: 2px; }
  .sachet .brand-name { font-size: 17px; }
  .sachet .brand-dot { width: 10px; height: 10px; }
  .sachet .product-name { font-size: 30px; margin: 6px 0 4px; }
  .sachet .description { font-size: 8.5px; }
  .sachet .gold-rule { width: 150px; margin: 5px 0 4px; }
  .sachet .description-fr { font-size: 7px; }
  .one-bag { font-size: 11px; letter-spacing: .1em; color: var(--gold); margin-top: 6px; }
  .sachet .lang-row { font-size: 10px; margin-top: 6px; }
</style>
</head>
<body>
<main class="canvas">

  <section class="panel back" aria-label="Back panel">
    <div class="kraft-band"></div>
    <div class="panel-body">
      <div class="brand-mark"><span class="brand-dot"></span><span class="brand-name">Velmora Brew</span></div>
      <p class="back-title">VELMORA GOLD</p>
      <p class="back-intro">Chai is a rich blend of strong and flavourful tea, aromatic spices, milk and sugar. Authentic chai is an art that requires all natural ingredients, care and time to prepare.</p>
      <h3>FOR 2 CUPS:</h3>
      <h3>INGREDIENTS:</h3>
      <ul>
        <li>1½ cups (12 oz) water</li>
        <li>2 chai tea bags</li>
        <li>1½ cups whole milk</li>
        <li>2–3 teaspoons sugar or honey to taste</li>
        <li>1–2 teaspoons sliced or grated fresh ginger (optional)</li>
      </ul>
      <h3>DIRECTIONS:</h3>
      <ol>
        <li>Bring water and tea bags to a low boil in a covered pot.</li>
        <li>Turn down heat, keep covered and simmer for 5 minutes.</li>
        <li>Add milk and sugar; stir and heat until steaming.</li>
        <li>Remove from heat and let stand for 2 minutes.</li>
        <li>Remove tea bags, pour into cups and enjoy.</li>
      </ol>
    </div>
    <div class="kraft-band"></div>
  </section>

  <div class="flap front-flap" aria-label="Top flap">
    <div class="kraft-band"></div>
    <div class="panel-body">
      <div class="brand-mark"><span class="brand-dot"></span><span class="brand-name">Velmora Brew</span></div>
    </div>
    <div class="kraft-band"></div>
  </div>

  <section class="panel front" aria-label="Front panel">
    <div class="kraft-band"></div>
    <div class="panel-body">
      <div class="lang-row"><span>CHAI TEA</span><span class="lang-sep"></span><span>THÉ CHAI</span></div>
      <div class="caffeine-row"><span>WITH CAFFEINE</span><span>AVEC LA CAFÉINE</span></div>
      <h1 class="product-name">Velmora Gold</h1>
      <p class="description">An exotic blend of black tea,<br>cardamon, fennel, cloves,<br>ginger and cinnamon</p>
      <div class="gold-rule"></div>
      <p class="description-fr">Un mélange exotique de thé noir, cardamome,<br>le fenouil, clous de girofle,<br>le gingembre et la cannelle</p>
      <div class="brand-mark"><span class="brand-dot"></span><span class="brand-name">Velmora Brew</span></div>
      <p class="count">18</p>
      <p class="count-label">TEA BAGS</p>
      <p class="small-print">Sachets de thé</p>
      <p class="small-print">No preservatives &amp; no artificial flavors</p>
      <p class="net-weight">NET WT 54 G (1.9 OZ)</p>
      <p class="small-print">Product of Alberta, Canada</p>
    </div>
    <div class="kraft-band"></div>
  </section>

  <section class="panel sachet" aria-label="Tea bag sachet">
    <div class="kraft-band"></div>
    <div class="panel-body">
      <div class="brand-mark"><span class="brand-dot"></span><span class="brand-name">Velmora Brew</span></div>
      <div class="lang-row"><span>CHAI TEA</span><span class="lang-sep"></span><span>THÉ CHAI</span></div>
      <h2 class="product-name">Velmora Gold</h2>
      <p class="description">An exotic blend of black tea, cardamon,<br>fennel, cloves, ginger and cinnamon</p>
      <div class="gold-rule"></div>
      <p class="description-fr">Un mélange exotique de thé noir, cardamome,<br>le fenouil, clous de girofle, le gingembre et la cannelle</p>
      <p class="one-bag">ONE TEA BAG</p>
    </div>
    <div class="kraft-band"></div>
  </section>

</main>
</body>
</html>
```